Business Card - Tidal Lanes

Need Business Card design for company named Tidal Lanes. Software development focused mainly on Brindle Orvix & Zelt Apps. I've attached our logo with both a black and white background. Please add trademark symbol to logo when using.

```html
<!DOCTYPE html>
<html lang="en">
<head>
<meta charset="utf-8">
<title>Tidal Lanes – Business Card</title>
<link rel="stylesheet" href="https://fonts.googleapis.com/css2?family=Nunito:wght@800&family=Open+Sans:wght@400;700&display=swap">
<style>
  :root {
    --page: #ece9e4;
    --metal-light: #b9bcbf;
    --metal-mid: #9a9da1;
    --metal-dark: #7e8185;
    --band-yellow: #f8bb15;
    --band-orange: #f59a33;
    --logo-orange: #f39a2c;
    --ink: #1d1d1d;
    --white: #ffffff;
  }
  * { box-sizing: border-box; margin: 0; padding: 0; }
  html, body { width: 1200px; height: 720px; overflow: hidden; background: var(--page); }
  .stage { position: relative; width: 1200px; height: 720px; }

  .card {
    position: absolute;
    width: 540px;
    height: 310px;
    overflow: hidden;
    border-radius: 4px;
    box-shadow: 0 10px 24px rgba(0,0,0,.18);
  }
  .card--front { left: 60px; top: 90px; }
  .card--back  { left: 600px; top: 320px; }

  .card__metal {
    position: absolute; inset: 0;
    background: linear-gradient(160deg, var(--metal-light) 0%, var(--metal-mid) 55%, var(--metal-dark) 100%);
  }

  .logo {
    position: absolute;
    display: flex;
    align-items: center;
    gap: 10px;
  }
  .logo__dot { border-radius: 50%; background: var(--logo-orange); flex: none; }
  .logo__name {
    font-family: "Nunito", sans-serif;
    font-weight: 800;
    color: var(--white);
    white-space: nowrap;
  }
  .card--front .logo { left: 190px; top: 40px; }
  .card--front .logo__dot { width: 30px; height: 30px; }
  .card--front .logo__name { font-size: 30px; }

  .card--back .logo { left: 50%; top: 50%; transform: translate(-50%, -50%); gap: 14px; }
  .card--back .logo__dot { width: 44px; height: 44px; }
  .card--back .logo__name { font-size: 46px; }

  .band {
    position: absolute; left: 0; right: 0; top: 140px; bottom: 0;
    background: linear-gradient(90deg, var(--band-yellow) 0%, var(--band-yellow) 45%, var(--band-orange) 100%);
  }
  .contact {
    position: absolute; left: 30px; top: 24px;
    font-family: "Open Sans", sans-serif;
    color: var(--ink);
  }
  .contact__name { font-size: 19px; font-weight: 700; margin-bottom: 6px; }
  .contact__title { font-weight: 400; font-size: 15px; }
  .contact__line { display: flex; align-items: center; gap: 8px; font-size: 14px; line-height: 24px; }
  .contact__line svg { width: 13px; height: 13px; fill: var(--ink); }
  .contact__address { font-size: 13px; margin-top: 6px; }
</style>
</head>
<body>
<main class="stage">

  <section class="card card--front" aria-label="Business card, front">
    <div class="card__metal" role="img" aria-label="Brushed steel texture"></div>
    <div class="logo">
      <span class="logo__dot"></span>
      <span class="logo__name">Tidal Lanes</span>
    </div>
    <div class="band">
      <div class="contact">
        <p class="contact__name">Your Name, <span class="contact__title">Title</span></p>
        <p class="contact__line">
          <svg viewBox="0 0 16 16" aria-hidden="true"><rect x="4" y="1" width="8" height="14" rx="1.5"/><rect x="5.5" y="3" width="5" height="7" fill="#f8bb15"/></svg>
          727-415-0382
        </p>
        <p class="contact__line">
          <svg viewBox="0 0 16 16" aria-hidden="true"><path d="M1 6c0-2 3-3 7-3s7 1 7 3v1h-3V5.5H4V7H1z"/><rect x="2" y="8" width="12" height="6" rx="1"/></svg>
          727-415-0917
        </p>
        <p class="contact__address">4410 Harbor Row, Dunmore, FL 33690</p>
      </div>
    </div>
  </section>

  <section class="card card--back" aria-label="Business card, back">
    <div class="card__metal" role="img" aria-label="Brushed steel texture"></div>
    <div class="logo">
      <span class="logo__dot"></span>
      <span class="logo__name">Tidal Lanes</span>
    </div>
  </section>

</main>
</body>
</html>
```